Maplecrest Disability - Social Security Disability Attorneys

Our company is expanding to attract clients nationwide for our social security disability practice. We have a logo, but I am looking for a creative and elegant letterhead that projects an image of being technologically advanced but still professional enough for the legal field. I am looking for the "wow factor" combined with this is still professional enough for a law practice.

Requesting letterhead and business card design
Updates

Had to update and change the logo. The previous logo had a typo. Please send updates with the new logo for consideration. The letterhead and business cards should be professional enough to be used for a law firm. Thanks.

Industry/Entity Type

Law Practice, Law Firm, Healthcare Industry, Government

Colors

Designer to choose colors to be used in the design.

Requirements
Nice to have
• **Please create a vertical design for the business card**

```html
<!DOCTYPE html>
<html lang="en">
<head>
<meta charset="utf-8">
<title>Maplecrest Disability – Stationery</title>
<link href="https://fonts.googleapis.com/css2?family=Marcellus&family=Open+Sans:wght@400;600&display=swap" rel="stylesheet">
<style>
  :root{
    --bg:#2b2e31;
    --paper:#ffffff;
    --blue:#0a9ae8;
    --navy:#1046c8;
    --orange:#ff7a0d;
    --sky:#46bdf5;
    --peach:#fdb877;
    --text:#3a3a3a;
    --muted:#8a8a8a;
    --pale-blue:#dcefff;
    --pale-peach:#ffe9d6;
  }
  *{margin:0;padding:0;box-sizing:border-box}
  html,body{width:1200px;height:960px;overflow:hidden;background:var(--bg)}
  .canvas{position:relative;width:1200px;height:960px;font-family:"Open Sans",sans-serif}

  .brand-name{font-family:"Marcellus",serif;color:var(--navy);font-weight:400;white-space:nowrap;display:flex;align-items:center;gap:7px}
  .brand-dot{width:9px;height:9px;border-radius:50%;background:var(--orange);flex:none}

  /* Letterhead */
  .letterhead{position:absolute;left:71px;top:41px;width:621px;height:878px;background:var(--paper);overflow:hidden}
  .letterhead .brand-name{position:absolute;left:20px;top:62px;font-size:23px}
  .lh-deco{position:absolute}
  .lh-contact{position:absolute;left:268px;top:37px;font-size:8px;font-weight:600;color:#2a7fd0;line-height:14px}
  .lh-contact .row{display:flex;align-items:center;gap:3px;white-space:nowrap}
  .ico{width:8px;height:8px;flex:none}
  .lh-bar{position:absolute;left:272px;right:0}
  .lh-bar.blue{top:65px;height:6px;background:var(--blue)}
  .lh-bar.orange{top:75px;height:7px;background:var(--orange)}
  .lh-foot{position:absolute;left:0;bottom:0;width:621px;height:7px}

  /* Card front */
  .card-front{position:absolute;left:578px;top:324px;width:357px;height:214px;
    background:linear-gradient(115deg,var(--blue) 0%,var(--sky) 28%,#b9b8a8 52%,var(--peach) 68%,var(--orange) 100%);
    box-shadow:0 10px 18px rgba(0,0,0,.35)}
  .card-front .brand-name{position:absolute;left:0;right:0;top:110px;justify-content:center;font-size:21px}
  .card-front .web{position:absolute;left:0;right:0;top:187px;text-align:center;font-size:10.5px;color:#1a1a1a}

  /* Card back */
  .card-back{position:absolute;left:786px;top:558px;width:361px;height:216px;background:var(--paper)}
  .card-back .brand-name{position:absolute;left:22px;top:44px;font-size:15.5px}
  .cb-band{position:absolute;left:25px;top:101px;width:336px;height:32px}
  .cb-person{position:absolute;right:17px;top:104px;text-align:right;color:#fff;line-height:1}
  .cb-person .name{font-size:11.5px;font-weight:600}
  .cb-person .role{font-size:7.5px;margin-top:2px}
  .cb-contact{position:absolute;left:14px;top:152px;font-size:8px;color:var(--muted);line-height:12.6px}
  .cb-contact .row{display:flex;align-items:center;gap:3px;white-space:nowrap}
  .cb-contact .row:first-child{color:var(--text)}
</style>
</head>
<body>
<div class="canvas">

  <section class="letterhead">
    <svg class="lh-deco" width="621" height="140" style="left:0;top:0" aria-hidden="true">
      <rect x="513" y="1" width="31" height="20" fill="var(--pale-peach)"/>
      <rect x="573" y="0" width="48" height="30" fill="var(--pale-blue)"/>
      <rect x="510" y="28" width="25" height="40" fill="#eeeeee"/>
      <rect x="546" y="21" width="28" height="50" fill="var(--pale-blue)"/>
      <rect x="598" y="49" width="23" height="20" fill="var(--pale-peach)"/>
      <rect x="511" y="77" width="34" height="16" fill="var(--pale-peach)"/>
      <rect x="546" y="84" width="48" height="76" rx="2" fill="var(--pale-blue)"/>
    </svg>
    <div class="brand-name">Maplecrest Disability<span class="brand-dot"></span></div>
    <div class="lh-contact">
      <div class="row"><svg class="ico" viewBox="0 0 10 10"><circle cx="5" cy="5" r="4.5" fill="none" stroke="var(--orange)"/><circle cx="5" cy="4.3" r="1.6" fill="var(--orange)"/></svg>0000 Example , Ste 135, California, 93103, United States</div>
      <div class="row"><svg class="ico" viewBox="0 0 10 10"><circle cx="5" cy="5" r="4.5" fill="none" stroke="var(--orange)"/><path d="M3.3 2.8c.6 2 1.6 3.3 3.4 4.2" stroke="var(--orange)" stroke-width="1.3" fill="none"/></svg>(000) 000-0000
        <svg class="ico" viewBox="0 0 10 10"><circle cx="5" cy="5" r="5" fill="var(--orange)"/><rect x="2.5" y="3.3" width="5" height="3.4" fill="#fff"/></svg>info@maplecrestdisability.com
        <svg class="ico" viewBox="0 0 10 10"><circle cx="5" cy="5" r="5" fill="var(--peach)"/></svg>www.maplecrestdisability.com</div>
    </div>
    <div class="lh-bar blue"></div>
    <div class="lh-bar orange"></div>
    <svg class="lh-foot" viewBox="0 0 621 7" preserveAspectRatio="none" aria-hidden="true">
      <polygon points="0,0 182,0 178,7 0,7" fill="var(--blue)"/>
      <polygon points="187,0 403,0 399,7 183,7" fill="var(--orange)"/>
      <polygon points="408,0 621,0 621,7 404,7" fill="var(--blue)"/>
    </svg>
  </section>

  <section class="card-front">
    <div class="brand-name">Maplecrest Disability<span class="brand-dot"></span></div>
    <div class="web">www.maplecrestdisability.com</div>
  </section>

  <section class="card-back">
    <div class="brand-name">Maplecrest Disability<span class="brand-dot"></span></div>
    <svg class="cb-band" viewBox="0 0 336 32" preserveAspectRatio="none" aria-hidden="true">
      <defs>
        <linearGradient id="fade" x1="0" x2="1">
          <stop offset="0" stop-color="#ffffff"/>
          <stop offset=".2" stop-color="#d8ecfa"/>
          <stop offset=".45" stop-color="#e6e6e6"/>
          <stop offset=".7" stop-color="var(--peach)"/>
          <stop offset="1" stop-color="var(--orange)"/>
        </linearGradient>
      </defs>
      <polygon points="0,0 336,0 336,32 190,32 165,8 0,8" fill="url(#fade)"/>
    </svg>
    <div class="cb-person">
      <div class="name">Example Name</div>
      <div class="role">Designation</div>
    </div>
    <div class="cb-contact">
      <div class="row"><svg class="ico" viewBox="0 0 10 10"><circle cx="5" cy="5" r="4.5" fill="#cfe6f7"/><circle cx="5" cy="4.5" r="1.5" fill="var(--blue)"/></svg>Level 00, 00 Example Street, Example 0</div>
      <div class="row"><svg class="ico" viewBox="0 0 10 10"><circle cx="5" cy="5" r="4.5" fill="#cfe6f7"/></svg>0000 000 129 <svg class="ico" viewBox="0 0 10 10"><circle cx="5" cy="5" r="4.5" fill="#cfe6f7"/></svg>0000 000 130</div>
      <div class="row"><svg class="ico" viewBox="0 0 10 10"><circle cx="5" cy="5" r="4.5" fill="#cfe6f7"/></svg>contact@maplecrestdisability.com <svg class="ico" viewBox="0 0 10 10"><circle cx="5" cy="5" r="4.5" fill="#fde0c4"/></svg>www.maplecrestdisability.com</div>
    </div>
  </section>

</div>
</body>
</html>
```